Holiday Rental Company Flyer Design (DL not A5)

Note from Brandloom Administration: The category sizing selected is A5, however the project requires DL sized artwork. Please refer to the DL template link below while the 'Special Requirements' are updated accordingly.

Project Brief:
We need a double sided DL flyer designed for an up market Holiday Rental Company that portrays a personalised approach to property management. These are to be used for letter box drops to homes we're specifically targeting so the design should be modern, complimentary colour palette, uncluttered & visually appealing.

Please Download the DL Template from Quillora here: http://www.quillora.com.au/ql/ns/propath/UploadResources.aspx?selectedTab=0?pfid=KMT&pf_id=KMT&xnav=easypath-upload-image#Templates

Target Market(s)

Wealthy Home Owners

Industry/Entity Type

It Company

Other font styles liked:
• Avant Garde Extra Light & Demi

Colors
33b8a4

Requirements
Must have
• DL Flyer sizes (210mm width x 99mm width, plus 3mm bleed)
• Front: Logo, Main Image & Grab
• Back: Contact Details & Brief Description of our business
• Images: Ideally the main image should be the house with the pool but alternatively a lifestyle images could also be used.
Nice to have
• A creative designer!
Should not have
• Clutter & busy designs

```html
<!DOCTYPE html>
<html lang="en">
<head>
<meta charset="utf-8">
<title>Coastward Stays – DL Flyer</title>
<link rel="stylesheet" href="https://fonts.googleapis.com/css2?family=Didact+Gothic&family=Montserrat:wght@600&display=swap">
<style>
  :root {
    --stage: #cbe3d5;
    --teal: #13a585;
    --teal-soft: #3aab8b;
    --ring-light: #7fd0bd;
    --ink: #6a6a6a;
    --white: #ffffff;
  }
  * { margin: 0; padding: 0; box-sizing: border-box; }
  html, body { width: 1200px; height: 1085px; overflow: hidden; }
  body { background: var(--stage); position: relative; font-family: "Didact Gothic", sans-serif; }

  .panel { position: absolute; top: 114px; width: 413px; height: 856px; overflow: hidden; }
  .panel--front { left: 132px; }
  .panel--back { left: 627px; background: var(--white); }

  /* front */
  .hero-photo { position: absolute; left: 0; top: 0; width: 413px; height: 576px;
    background: linear-gradient(100deg, #2b2630 0%, #5a4a68 25%, #b08a5c 42%, #8fa8a6 60%, #a9c2bd 100%); }
  .hero-pool { position: absolute; left: 0; top: 500px; width: 260px; height: 76px;
    background: linear-gradient(90deg, #2a64b8, #4aa0d8); }
  .hero-wash { position: absolute; inset: 0; width: 413px; height: 576px; }
  .detail { position: absolute; border-radius: 50%; border: 5px solid var(--teal); }
  .detail--flowers { left: 136px; top: 22px; width: 130px; height: 130px;
    background: radial-gradient(circle at 45% 45%, #c8885a, #6e5a4c 70%); }
  .detail--bedroom { left: 160px; top: 182px; width: 156px; height: 156px; border-color: var(--ring-light);
    background: radial-gradient(circle at 55% 45%, #d9d23e, #c9a98a 55%, #e8ddd0); }
  .detail--basin { left: 189px; top: 398px; width: 168px; height: 168px;
    background: radial-gradient(circle at 50% 60%, #f0eeea, #b9b8b2 75%); }
  .brand-band { position: absolute; left: 0; top: 576px; width: 413px; height: 280px; background: var(--teal-soft); }
  .brand-name { position: absolute; left: 0; top: 60px; width: 100%; text-align: center; color: var(--white);
    font-size: 44px; letter-spacing: 4px; line-height: 52px; text-transform: uppercase; }
  .brand-dot { position: absolute; left: 188px; top: 182px; width: 38px; height: 38px;
    border: 1.5px solid var(--white); border-radius: 50%; }

  /* back */
  .section-head { position: absolute; left: 0; top: 58px; width: 100%; height: 91px; background: var(--teal);
    color: var(--white); font-family: "Montserrat", sans-serif; font-weight: 600; font-size: 23px;
    display: flex; align-items: center; justify-content: center; }
  .about { position: absolute; left: 48px; top: 170px; width: 330px; color: var(--ink); font-size: 16.5px; line-height: 20.4px; }
  .about p { margin-bottom: 20.4px; }
  .contact-band { position: absolute; left: 0; top: 576px; width: 100%; height: 175px; background: var(--teal); color: var(--white);
    font-family: "Montserrat", sans-serif; font-weight: 600; }
  .contact-list { list-style: none; position: absolute; left: 63px; top: 18px; font-size: 15.5px; line-height: 28.5px; }
  .postal { position: absolute; left: 0; top: 124px; width: 100%; text-align: center; font-size: 21px; }
  .coast-photo { position: absolute; top: 751px; height: 105px; }
  .coast-photo--boat { left: 0; width: 205px; background: linear-gradient(180deg, #c9cdd0 0%, #a7b6bf 55%, #7f9fae 100%); }
  .coast-photo--seals { left: 206px; width: 207px; background: linear-gradient(160deg, #3fc1c2, #1e9ea5); }
</style>
</head>
<body>
  <section class="panel panel--front">
    <div class="hero-photo" role="img" aria-label="Modern holiday home at dusk with lit glass walls beside a pool"></div>
    <div class="hero-pool" aria-hidden="true"></div>
    <svg class="hero-wash" viewBox="0 0 413 576" aria-hidden="true">
      <path d="M120 0 C250 120 240 360 300 576 L413 576 L413 0 Z" fill="#9fbab5" opacity="0.75"/>
      <path d="M120 0 C250 120 240 360 300 576" fill="none" stroke="#dfe8e6" stroke-width="10" opacity="0.8"/>
      <path d="M150 0 C275 130 260 360 320 576" fill="none" stroke="#6fbfae" stroke-width="4" opacity="0.6"/>
    </svg>
    <div class="detail detail--flowers" role="img" aria-label="Vase of orange tropical flowers on a table"></div>
    <div class="detail detail--bedroom" role="img" aria-label="Bed with yellow cushions and a colourful throw"></div>
    <div class="detail detail--basin" role="img" aria-label="Bathroom basin with orchids and tiled wall"></div>
    <div class="brand-band">
      <div class="brand-name">Coastward<br>Stays</div>
      <div class="brand-dot" aria-hidden="true"></div>
    </div>
  </section>

  <section class="panel panel--back">
    <h2 class="section-head">What we do differently!</h2>
    <div class="about">
      <p>&nbsp;&nbsp;Rather than relying upon a key safe or a central pick-up destination, a ‘Coast-ward Stays’ staff member will greet guests upon arrival.</p>
      <p>&nbsp;&nbsp;Our ‘Meet &amp; Greet’ service provides home owners with an increased level of Security and also allows us to:</p>
      <p>&nbsp;&nbsp;Prepare the home for their arrival (lights, heaters, music etc.)<br>&nbsp;&nbsp;Establish a rapport &amp; help facilitate future bookings<br>&nbsp;&nbsp;Reiterate their responsibilities to ensure the return of their bond</p>
      <p>&nbsp;&nbsp;If you’d like to know what your proper-ty could achieve or require additional information, please contact us on:</p>
    </div>
    <div class="contact-band">
      <ul class="contact-list">
        <li>t: (03)5900 4127</li>
        <li>e: stay@coastwardstays.com.au</li>
        <li>w: coastwardstays.com.au</li>
      </ul>
      <p class="postal">PO Box 18, Seacliff Victoria 3905</p>
    </div>
    <div class="coast-photo coast-photo--boat" role="img" aria-label="Small sailing boat on a calm bay"></div>
    <div class="coast-photo coast-photo--seals" role="img" aria-label="Seals swimming in turquoise water"></div>
  </section>
</body>
</html>
```